KBT Business Cards

We require business cards for our business. We would like a matte black back to the card, with our logo centred in the middle. The front side of the card is open to design.

Target Market(s)

Clients looking for legal services (professional)

Industry/Entity Type

Legal

Contact Information for Business Card

Doran Kelbrath
Partner
Mobile: 0461 738 524
Email: doran@kbtlaw.co
Website: www.kbtlaw.co
Level 3, 118 Wendmore Street
Sydney NSW 2000

Font styles to use
Other font styles liked:
• Avenir

Colors
f04a50
ffffff
1b1b1b

Requirements
Must have
• Black back with logo included in the centre of the card.
• Our font is Avenir.

```html
<!DOCTYPE html>
<html lang="en">
<head>
<meta charset="utf-8">
<title>KBT Business Cards</title>
<link rel="stylesheet" href="https://fonts.googleapis.com/css2?family=Nunito+Sans:wght@400;600;800&display=swap">
<style>
  :root {
    --page-bg: #e9e6e1;
    --card-white: #ffffff;
    --card-black: #1b1b1b;
    --accent: #d62d64;
    --ink: #1b1b1b;
    --paper-text: #ffffff;
    --muted-text: #e6e6e6;
  }
  * { box-sizing: border-box; margin: 0; padding: 0; }
  html, body {
    width: 1200px; height: 780px; overflow: hidden;
    background: var(--page-bg);
    font-family: "Nunito Sans", "Avenir", sans-serif;
  }
  .canvas {
    position: relative; width: 1200px; height: 780px;
  }
  .card {
    position: absolute; top: 235px;
    width: 540px; height: 309px;
    overflow: hidden;
    box-shadow: 0 10px 28px rgba(0,0,0,0.22);
  }
  .card-front { left: 40px; background: var(--card-white); }
  .card-back  { left: 620px; background: var(--card-black); }

  .front-shapes { position: absolute; inset: 0; }

  .firm-name {
    position: absolute; left: 44px; top: 52px;
    display: flex; align-items: flex-start; gap: 14px;
  }
  .firm-square { width: 22px; height: 22px; background: var(--accent); margin-top: 4px; flex: none; }
  .firm-words {
    font-weight: 800; font-size: 22px; line-height: 1.02;
    letter-spacing: 0.02em; text-transform: uppercase; color: var(--ink);
  }

  .name-line {
    position: absolute; left: 40px; top: 163px;
    display: flex; align-items: center; gap: 10px;
    color: var(--paper-text); font-size: 14px; line-height: 22px;
  }
  .person-name { font-weight: 800; text-transform: uppercase; letter-spacing: 0.03em; }
  .divider { width: 1.5px; height: 16px; background: var(--paper-text); }
  .person-role { font-weight: 400; }

  .contact-list {
    position: absolute; left: 40px; top: 204px;
    list-style: none; color: var(--muted-text);
    font-size: 12.5px; line-height: 1;
  }
  .contact-list li { display: flex; align-items: center; gap: 9px; margin-bottom: 9px; }
  .contact-list .sep { margin: 0 8px; }
  .icon {
    width: 16px; height: 16px; border-radius: 50%;
    background: var(--accent); flex: none;
    display: flex; align-items: center; justify-content: center;
  }
  .icon svg { width: 9px; height: 9px; }

  .back-mark {
    position: absolute; inset: 0;
    display: flex; align-items: center; justify-content: center; gap: 16px;
  }
  .back-mark .firm-square { width: 28px; height: 28px; margin-top: 4px; }
  .back-mark .firm-words { color: var(--paper-text); font-size: 26px; }
</style>
</head>
<body>
<main class="canvas">

  <section class="card card-front" aria-label="Business card front">
    <svg class="front-shapes" viewBox="0 0 540 309" aria-hidden="true">
      <polyline points="-10,174 328,174 456,-4" fill="none" stroke="var(--accent)" stroke-width="30" stroke-linejoin="miter"/>
      <polygon points="0,189 337,189 475,0 540,0 540,309 0,309" fill="var(--card-black)"/>
    </svg>

    <div class="firm-name">
      <span class="firm-square"></span>
      <p class="firm-words">Kelbrath<br>Brandt Tovey<br>Legal</p>
    </div>

    <p class="name-line">
      <span class="person-name">Doran Kelbrath</span>
      <span class="divider"></span>
      <span class="person-role">Partner</span>
    </p>

    <ul class="contact-list">
      <li>
        <span class="icon"><svg viewBox="0 0 10 10"><path d="M2 1h2l1 2.5-1.2.8a5 5 0 0 0 2 2l.8-1.2L9 6v2a1 1 0 0 1-1 1A7 7 0 0 1 1 2a1 1 0 0 1 1-1z" fill="#fff"/></svg></span>
        <span>0461 738 524</span><span class="sep">|</span>
        <span class="icon"><svg viewBox="0 0 10 10"><rect x="1" y="2.5" width="8" height="5.5" fill="none" stroke="#fff" stroke-width="1.2"/><path d="M1 2.5l4 3 4-3" fill="none" stroke="#fff" stroke-width="1.2"/></svg></span>
        <span>doran@kbtlaw.co</span>
      </li>
      <li>
        <span class="icon"><svg viewBox="0 0 10 10"><circle cx="5" cy="5" r="3.8" fill="none" stroke="#fff" stroke-width="1.1"/><path d="M1.2 5h7.6M5 1.2c-2 2.4-2 5.2 0 7.6M5 1.2c2 2.4 2 5.2 0 7.6" fill="none" stroke="#fff" stroke-width="0.9"/></svg></span>
        <span>www.kbtlaw.co</span>
      </li>
      <li>
        <span class="icon"><svg viewBox="0 0 10 10"><path d="M5 9.5S1.8 6 1.8 4a3.2 3.2 0 0 1 6.4 0C8.2 6 5 9.5 5 9.5z" fill="#fff"/><circle cx="5" cy="4" r="1.1" fill="var(--accent)"/></svg></span>
        <span>Level 3, 118 Wendmore Street. Sydney NSW 2000</span>
      </li>
    </ul>
  </section>

  <section class="card card-back" aria-label="Business card back">
    <div class="back-mark">
      <span class="firm-square"></span>
      <p class="firm-words">Kelbrath<br>Brandt Tovey<br>Legal</p>
    </div>
  </section>

</main>
</body>
</html>
```